New Business Card Design Project

Use the flyer uploaded and website www.brightoakbuilders.com for inspiration.
List Our Services on Backside of business cards
Marcus Delling
Harborline Builders Inc.
Licensed General Contractors
858-471-6093

Contact Information for Business Card

Use the flyer uploaded and website www.brightoakbuilders.com for inspiration. List Our Services on Backside of business cards Marcus Delling Harborline Builders Inc. Licensed General Contractors 858-471-6093

```html
<!DOCTYPE html>
<html lang="en">
<head>
<meta charset="utf-8">
<title>Harborline Builders Business Card</title>
<link href="https://fonts.googleapis.com/css2?family=Cinzel:wght@600&family=Montserrat:wght@400;500&display=swap" rel="stylesheet">
<style>
  :root {
    --page-bg: #0b0b0c;
    --card-bg: #151517;
    --ink: #f4f4f4;
    --ink-soft: #d9d9d9;
  }
  * { box-sizing: border-box; margin: 0; padding: 0; }
  html, body {
    width: 1200px; height: 912px; overflow: hidden;
    background: var(--page-bg);
    font-family: "Montserrat", sans-serif;
    color: var(--ink);
  }
  .canvas { position: relative; width: 1200px; height: 912px; }
  .card {
    position: absolute;
    width: 620px; height: 354px;
    background: var(--card-bg);
    border-radius: 16px;
    box-shadow: 0 18px 40px rgba(0,0,0,0.6);
    overflow: hidden;
  }
  .card--services { left: 120px; top: 70px; }
  .card--contact { left: 460px; top: 488px; }

  /* brand wordmark */
  .brand { display: flex; align-items: center; gap: 12px; white-space: nowrap; }
  .brand__dot {
    width: 14px; height: 14px; border-radius: 50%;
    background: var(--ink); flex: none;
  }
  .brand__name {
    font-family: "Montserrat", sans-serif;
    font-weight: 500;
    letter-spacing: 3px;
    text-transform: uppercase;
    color: var(--ink);
  }

  /* services side */
  .card--services .brand {
    position: absolute; left: 0; right: 0; top: 120px;
    justify-content: center;
  }
  .card--services .brand__name { font-size: 26px; }
  .services {
    position: absolute; left: 0; right: 0; top: 226px;
    text-align: center;
    font-size: 17px; line-height: 30px;
    color: var(--ink-soft);
    letter-spacing: 0.3px;
  }

  /* contact side */
  .card--contact .brand { position: absolute; left: 30px; top: 130px; }
  .card--contact .brand__dot { width: 12px; height: 12px; }
  .card--contact .brand__name { font-size: 15px; letter-spacing: 1px; }
  .divider {
    position: absolute; left: 318px; top: 40px;
    width: 1px; height: 170px; background: var(--ink);
  }
  .person { position: absolute; left: 342px; top: 46px; }
  .person__name {
    font-family: "Cinzel", serif; font-weight: 600;
    font-size: 24px; letter-spacing: 1px; line-height: 1.1;
    white-space: nowrap;
  }
  .person__title { font-size: 14px; margin-top: 4px; color: var(--ink-soft); }
  .contact-list { list-style: none; position: absolute; left: 342px; top: 138px; }
  .contact-list li {
    display: flex; align-items: center; gap: 10px;
    font-size: 14px; line-height: 26px; color: var(--ink-soft);
    white-space: nowrap;
  }
  .contact-list svg { width: 13px; height: 13px; fill: var(--ink); flex: none; }
  .footer-rule {
    position: absolute; left: 0; right: 0; top: 290px;
    display: flex; align-items: center; gap: 14px;
  }
  .footer-rule__line { height: 1px; background: var(--ink); }
  .footer-rule__line--left { flex: 1.3; }
  .footer-rule__line--right { flex: 0.35; }
  .footer-rule__text { font-size: 15px; color: var(--ink); white-space: nowrap; }
</style>
</head>
<body>
<main class="canvas">

  <section class="card card--services" aria-label="Business card back, services">
    <div class="brand">
      <span class="brand__dot"></span>
      <span class="brand__name">Harborline Builders</span>
    </div>
    <p class="services">
      Painting • Flooring • Kitchens • Custom Renovations<br>
      Bathrooms • Energy Efficienct Upgrades
    </p>
  </section>

  <section class="card card--contact" aria-label="Business card front, contact details">
    <div class="brand">
      <span class="brand__dot"></span>
      <span class="brand__name">Harborline Builders</span>
    </div>
    <div class="divider"></div>
    <div class="person">
      <h1 class="person__name">MARCUS DELLING</h1>
      <p class="person__title">Licensed General Contractors</p>
    </div>
    <ul class="contact-list">
      <li>
        <svg viewBox="0 0 24 24" aria-hidden="true"><path d="M6.6 10.8a15 15 0 0 0 6.6 6.6l2.2-2.2a1 1 0 0 1 1-.25 11.4 11.4 0 0 0 3.6.57 1 1 0 0 1 1 1V20a1 1 0 0 1-1 1A17 17 0 0 1 3 4a1 1 0 0 1 1-1h3.5a1 1 0 0 1 1 1c0 1.25.2 2.450.57 3.57a1 1 0 0 1-.25 1z"/></svg>
        858-471-6093
      </li>
      <li>
        <svg viewBox="0 0 24 24" aria-hidden="true"><path d="M2 5h20v14H2z M3.5 6.5 12 13l8.5-6.5" fill="none" stroke="#f4f4f4" stroke-width="2"/></svg>
        info@brightoakbuilders.com
      </li>
      <li>
        <svg viewBox="0 0 24 24" aria-hidden="true"><circle cx="12" cy="12" r="10"/></svg>
        www.brightoakbuilders.com
      </li>
    </ul>
    <div class="footer-rule">
      <span class="footer-rule__line footer-rule__line--left"></span>
      <span class="footer-rule__text">Harborline Builders Inc.</span>
      <span class="footer-rule__line footer-rule__line--right"></span>
    </div>
  </section>

</main>
</body>
</html>
```